Growing the Ironclad Young Contender:
A Family Playbook for Nurturing Bold, Grounded, and Resilient Daughters at Games and Beyond.
📘 Book Cover Design Brief – “Growing the Ironclad Young Contender”

Project Title:
Design a bold, inspiring book cover for a best-selling book titled:
Growing the Ironclad Young Contender
Subtitle: A Family Playbook for Nurturing Bold, Grounded, and Resilient Daughters at Games and Beyond

🎯 Audience:

Parents of female athletes ages 14–20 who want their daughters to build confidence, strength, resilience, and long-term success both in sports and in life.

This book should feel encouraging, empowering, and credible — NOT cheesy, childish, or overly academic.

📕 Design Tone & Style:

Powerful and professional — should feel like a best-selling book from a leading performance or parenting expert

Emotionally compelling — conveys hope, resilience, strength, and possibility

Visually modern and clean — avoid anything overly busy, cliché, or childish

Heroic/aspirational tone — think transformation, leadership, strong positioning

💡 Visual Direction / Ideas (Use as Inspiration, Not Limitation):

Strong, confident teenage female athlete imagery — adaptable beyond one specific sport

Symbolic visuals — e.g. athlete standing strong, on a starting line, looking bold into the future, silhouette, or power stance

Bold typography that feels clean and modern (e.g., Proxima Nova, Montserrat, Gotham, Bebas Neue, etc.)

A title that stands out clearly when viewed as a thumbnail on Brindlemart

Color tones: Empowering, modern, and strong: think deep blues, greens, purples, or golds — avoid playful pastels or overly girly themes

Potential imagery: textured backgrounds, motion, bravery, development, strength, growth, sport/action overlays

🔥 What the Cover MUST Communicate:

✅ This is for parents who want strong, confident female athletes
✅ It’s a guidebook for personal development AND sports performance
✅ It’s about creating “IRONCLAD” confidence — physically, mentally and emotionally
✅ The message is: You can help your daughter become her strongest, most confident self

📚 Back-of-Book Summary (for context):

"Growing the Ironclad Young Contender" is a parent's blueprint to building girls who are strong in body, confident in mind, and ready to lead on and off the field. Through simple strategies around strength training, mindset, nutrition, and character development, this book gives parents the tools to help their daughters stay injury-resistant, break through mental barriers, and unlock their full potential — in sports and in life.

✅ Deliverables:

Full cover design (front, back, spine) for paperback
High-resolution files (print-ready)
Source files (PSD, AI, etc.)
3D mockup versions of the book (standing, flat, stack)

Target Market(s)

Industry/Entity Type

Fitness

Font styles to use
Sans Serif

Colors
FFF300
FFF600
FEFA6F
FFFEC7
FFFEE8

Requirements
Must have
• Bold Font
Should not have
• I don't want an image of a female athlete. I want this to be font based.

```html
<!DOCTYPE html>
<html lang="en">
<head>
<meta charset="utf-8">
<title>Growing the Ironclad Young Contender – Cover</title>
<link rel="stylesheet" href="https://fonts.googleapis.com/css2?family=Bebas+Neue&family=Montserrat:wght@500;700;800&display=swap">
<style>
  :root {
    --page-bg: #ededed;
    --cover-black: #0c0c0c;
    --cover-charcoal: #1d1d1d;
    --gold: #ffcc00;
    --gold-deep: #b8920a;
    --white: #ffffff;
  }
  * { margin: 0; padding: 0; box-sizing: border-box; }
  html, body {
    width: 1200px;
    height: 1200px;
    overflow: hidden;
    background: var(--page-bg);
  }
  .cover {
    position: absolute;
    left: 200px;
    top: 0;
    width: 800px;
    height: 1200px;
    overflow: hidden;
    background:
      radial-gradient(ellipse at 30% 12%, rgba(60,60,60,0.55) 0%, rgba(0,0,0,0) 45%),
      radial-gradient(ellipse at 80% 70%, rgba(40,40,40,0.5) 0%, rgba(0,0,0,0) 50%),
      linear-gradient(180deg, var(--cover-charcoal) 0%, var(--cover-black) 60%, #070707 100%);
    font-family: "Montserrat", sans-serif;
    color: var(--white);
  }
  .brand {
    position: absolute;
    left: 0;
    top: 36px;
    width: 800px;
    display: flex;
    flex-direction: column;
    align-items: center;
    gap: 14px;
  }
  .brand-dot {
    width: 66px;
    height: 66px;
    border-radius: 50%;
    border: 3px solid var(--gold-deep);
  }
  .brand-name {
    font-family: "Montserrat", sans-serif;
    font-weight: 800;
    font-size: 22px;
    letter-spacing: 3px;
    color: var(--white);
  }
  .hero-art {
    position: absolute;
    left: 477px;
    top: 94px;
    width: 257px;
    height: 384px;
  }
  .title {
    position: absolute;
    left: 0;
    top: 412px;
    width: 800px;
    text-align: center;
  }
  .title-line {
    display: block;
    font-family: "Montserrat", sans-serif;
    font-weight: 800;
    color: var(--white);
    line-height: 1;
  }
  .title-top { font-size: 74px; letter-spacing: -1px; }
  .title-key {
    font-family: "Bebas Neue", sans-serif;
    font-weight: 400;
    font-size: 200px;
    letter-spacing: 6px;
    color: var(--gold);
    line-height: 0.78;
    margin-top: 14px;
  }
  .title-bottom { font-size: 62px; letter-spacing: -1px; margin-top: 10px; }
  .subtitle {
    position: absolute;
    left: 0;
    top: 764px;
    width: 800px;
    text-align: center;
    font-weight: 500;
    font-size: 28px;
    letter-spacing: 3px;
    line-height: 48px;
    text-transform: uppercase;
  }
  .subtitle .accent { color: var(--gold); }
  .author {
    position: absolute;
    left: 0;
    top: 1086px;
    width: 800px;
    text-align: center;
    font-family: "Bebas Neue", sans-serif;
    font-size: 66px;
    letter-spacing: 5px;
    color: var(--gold);
    line-height: 1;
  }
</style>
</head>
<body>
  <main class="cover">
    <header class="brand">
      <span class="brand-dot"></span>
      <span class="brand-name">IRONCLAD</span>
    </header>

    <svg class="hero-art" viewBox="0 0 257 384" role="img" aria-label="Gold silhouette of a young athlete leaping upward with a ball">
      <defs>
        <radialGradient id="heroGlow" cx="50%" cy="50%" r="60%">
          <stop offset="0%" stop-color="#ffcc00" stop-opacity="0.85"/>
          <stop offset="100%" stop-color="#ffcc00" stop-opacity="0"/>
        </radialGradient>
      </defs>
      <rect width="257" height="384" fill="url(#heroGlow)"/>
    </svg>

    <h1 class="title">
      <span class="title-line title-top">GROWING THE</span>
      <span class="title-line title-key">IRONCLAD</span>
      <span class="title-line title-bottom">YOUNG CONTENDER</span>
    </h1>

    <p class="subtitle">
      A family playbook for<br>
      nurturing <span class="accent">bold, grounded,</span><br>
      <span class="accent">and resilient</span> daughters<br>
      at games and beyond
    </p>

    <p class="author">RYLAN MADDOX</p>
  </main>
</body>
</html>
```